Heritage Hollow Business Cards

Require a business card design. <br/><br/>Needs to include logo (either round or long version) plus these details:<br/>Maya Torvell<br/>Heritage Hollow<br/>maya@kelvadtrading.com.au<br/>02 6481 7395<br/>PO Box Glenwarra NSW 2791<br/>www.heritagehollow.com.au<br/><br/>I need in an editable format so that I can create for multiple staff members. <br/><br/>

Target Market(s)

We are an online store selling renovation products to home owners are builders. Looking for a classic classy design.

Industry/Entity Type

Home And Garden

Contact Information for Business Card

Maya Torvell
Heritage Hollow
maya@kelvadtrading.com.au
02 6481 7395
PO Box Glenwarra NSW 2791
www.heritagehollow.com.au

Colors

Designer to choose colors to be used in the design.

Requirements
Must have
• Must include Logo.

```html
<!DOCTYPE html>
<html lang="en">
<head>
<meta charset="utf-8">
<title>Heritage Hollow Business Cards</title>
<link rel="stylesheet" href="https://fonts.googleapis.com/css2?family=Cormorant+Garamond:wght@600&family=Roboto:wght@400;500;700&display=swap">
<style>
  :root {
    --page: #e4e5e8;
    --card-dark: #0c0c0c;
    --card-dark-edge: #161616;
    --card-light: #ededed;
    --ink: #141414;
    --ink-soft: #2a2a2a;
    --mark-faint: #5a5a5a;
    --ring-faint: #3c3c3c;
  }
  * { margin: 0; padding: 0; box-sizing: border-box; }
  html, body { width: 1200px; height: 1200px; overflow: hidden; }
  body { background: var(--page); position: relative; font-family: "Roboto", Arial, sans-serif; }

  .card {
    position: absolute;
    left: 269px;
    width: 663px;
    height: 379px;
    border-radius: 18px;
    overflow: hidden;
  }
  .card--front {
    top: 178px;
    background: radial-gradient(ellipse at 60% 20%, var(--card-dark-edge), var(--card-dark) 70%);
  }
  .card--back { top: 643px; background: var(--card-light); }

  .brand-serif { font-family: "Cormorant Garamond", Georgia, serif; font-weight: 600; }

  .front-ring {
    position: absolute;
    left: 134px; top: 109px;
    width: 146px; height: 146px;
    border: 1.5px solid var(--ring-faint);
    border-radius: 50%;
  }
  .front-name {
    position: absolute;
    left: 151px; top: 196px;
    font-size: 50px;
    line-height: 1;
    color: var(--mark-faint);
    letter-spacing: 0.5px;
  }

  .back-ring {
    position: absolute;
    left: 152px; top: 114px;
    width: 140px; height: 140px;
    border: 1.5px solid var(--ink);
    border-radius: 50%;
  }
  .back-name-mark {
    position: absolute;
    left: 152px; top: 151px;
    width: 140px;
    text-align: center;
    font-size: 23px;
    line-height: 1.05;
    color: var(--ink);
  }
  .divider {
    position: absolute;
    left: 311px; top: 122px;
    width: 1.5px; height: 134px;
    background: var(--ink-soft);
  }
  .contact {
    position: absolute;
    left: 328px; top: 120px;
    color: var(--ink);
  }
  .contact__person {
    font-size: 29px;
    line-height: 1;
    letter-spacing: 0.3px;
    text-transform: uppercase;
  }
  .contact__company {
    margin-top: 12px;
    font-size: 16px;
    font-weight: 500;
    letter-spacing: 0.2px;
    text-transform: uppercase;
  }
  .contact__list { list-style: none; margin-top: 7px; }
  .contact__item {
    display: flex;
    align-items: center;
    gap: 6px;
    height: 19.5px;
    font-size: 12.8px;
    color: var(--ink-soft);
  }
  .contact__item svg { width: 10px; height: 10px; flex: none; fill: var(--ink); }
  .contact__item strong { font-weight: 700; color: var(--ink); }
</style>
</head>
<body>
  <section class="card card--front" aria-label="Card front">
    <div class="front-ring"></div>
    <div class="front-name brand-serif">Heritage Hollow</div>
  </section>

  <section class="card card--back" aria-label="Card back">
    <div class="back-ring"></div>
    <div class="back-name-mark brand-serif">Heritage<br>Hollow</div>
    <div class="divider"></div>
    <div class="contact">
      <div class="contact__person brand-serif">Maya Torvell</div>
      <div class="contact__company">Heritage Hollow</div>
      <ul class="contact__list">
        <li class="contact__item">
          <svg viewBox="0 0 10 10" aria-hidden="true"><path d="M5 0a3.5 3.5 0 0 0-3.5 3.5C1.5 6 5 10 5 10s3.5-4 3.5-6.5A3.5 3.5 0 0 0 5 0zm0 5a1.4 1.4 0 1 1 0-2.8A1.4 1.4 0 0 1 5 5z"/></svg>
          PO Box Glenwarra NSW 2791
        </li>
        <li class="contact__item">
          <svg viewBox="0 0 10 10" aria-hidden="true"><path d="M2 .5l1.6 2.2-.9 1.1c.6 1.3 1.5 2.2 2.8 2.8l1.1-.9L8.8 7.3 8 9.2C4.3 9 1 5.7.8 2z"/></svg>
          02 6481 7395
        </li>
        <li class="contact__item">
          <svg viewBox="0 0 10 10" aria-hidden="true"><path d="M0 2h10v6.5H0zm1 1v.3l4 2.5 4-2.5V3z"/></svg>
          maya@kelvadtrading.com.au
        </li>
        <li class="contact__item">
          <svg viewBox="0 0 10 10" aria-hidden="true"><path d="M5 0a5 5 0 1 0 0 10A5 5 0 0 0 5 0zm3.9 4.5H7.1a7 7 0 0 0-.9-3.3 4 4 0 0 1 2.7 3.3zM5 1.1c.6.8 1 2 1.1 3.4H3.9C4 3.1 4.4 1.9 5 1.1zM3.8 1.2a7 7 0 0 0-.9 3.3H1.1a4 4 0 0 1 2.7-3.3zM1.1 5.5h1.8a7 7 0 0 0 .9 3.3 4 4 0 0 1-2.7-3.3zM5 8.9c-.6-.8-1-2-1.1-3.4h2.2C6 6.9 5.6 8.1 5 8.9zm1.2-.1a7 7 0 0 0 .9-3.3h1.8a4 4 0 0 1-2.7 3.3z"/></svg>
          <span>www.<strong>heritagehollow</strong>.com.au</span>
        </li>
      </ul>
    </div>
  </section>
</body>
</html>
```